Need website for Dating "Game" App

I need a one or two page website for a new dating "game" app (patent pending) called wooSpark.net. The game will be "interactive" and is designed to be a fun, safe and nonthreatening way to help two people get to know more about each other "before making a face to face date". The App will be configured somewhat like a dating app/website where members browse profiles to find someone they are interested in getting to know.
I am looking for a design that will capture the attention of singles who are tired of wasting time on face to face dates with individuals they are not compatible with. This website will be used as somewhat of a launch page for a Fundlaunch campaign because the app is still in the development stage.

Target Market(s)

Single daters who are looking for a compatible mate

Industry/Entity Type

Dating

Number of Pages Required

2 page

Requirements
Must have
• Mention that the game is Patent Pending
• Must be whimsical but with a classy-clean look (the game is designed to be fun)
• I have a 30 second video completed that I would like incorporated on the website.
• Logo colors must stay the same
• Page must direct to my upcoming Fundlaunch campaign - (Dating App is still in development stage)
Nice to have
• 1. The game will populate relationship/lifestyle like questions to two players who opt to play the game together. The design could possibly have some fun relationship questions "raining" down on the page.
• 2. Tag line...MEET - PLAY - DATE (T.M.)
• Meet - Browse profiles to find someone whom you want to get to know better and invite them to play!
• Play - Many dating sites take you through a grueling set of questions before you upload a profile. You are then matched with individuals that an "algorithm" determines you are most compatible with. The problem with this method is that only the algorithm knows what areas you and those individuals have in common. WooSpark.net alleviates the guesswork by placing the power of the algorithm in your hands with a fun, safe and nonthreatening game that helps you get to know your person of interest before meeting face to face!
• Date -
• 3. "Wouldn't it be great to get to know someone better before making a date?"
Should not have
• Nothing raunchy.
• I don't want the basic 'dating website' look (although I do like the "Tulip Finds Lantern" site.

```html
<!DOCTYPE html>
<html lang="en">
<head>
<meta charset="utf-8">
<title>wooSpark.net — Meet · Play · Date</title>
<link rel="stylesheet" href="https://fonts.googleapis.com/css2?family=Raleway:wght@300;400;500;700;800&family=Open+Sans:wght@400;600&display=swap">
<style>
:root{
  --red:#e5322d;
  --red-deep:#c8262a;
  --ink:#333333;
  --muted:#555555;
  --line:#e0e0e0;
  --soft:#f4f4f4;
  --white:#ffffff;
  --heading:"Raleway",sans-serif;
  --body:"Open Sans",sans-serif;
}
*{box-sizing:border-box;margin:0;padding:0}
html,body{width:1200px;height:2624px;overflow:hidden;background:var(--white)}
body{position:relative;font-family:var(--body);color:var(--ink)}
.center{text-align:center}

/* header */
.site-header{position:absolute;left:0;top:0;width:1200px;height:119px;border-top:3px solid var(--red);background:var(--white)}
.brand{position:absolute;left:131px;top:48px;display:flex;align-items:center;gap:9px}
.brand-dot{width:20px;height:20px;border-radius:50%;background:var(--red)}
.brand-name{font-family:var(--heading);font-weight:800;font-size:27px;line-height:32px;color:var(--red);letter-spacing:-.3px}
.main-nav{position:absolute;top:58px;left:0;width:1200px;font-family:var(--heading);font-size:13px;color:var(--ink)}
.main-nav a{position:absolute;color:inherit;text-decoration:none;white-space:nowrap}
.main-nav a.active{color:var(--red)}
.btn{display:flex;align-items:center;justify-content:center;border-radius:22px;font-family:var(--heading);font-size:14px;text-transform:uppercase;text-decoration:none}
.btn-red{background:linear-gradient(#ef4a3f,#dd2d28);color:var(--white)}
.nav-cta{position:absolute;left:962px;top:48px;width:106px;height:36px;font-size:13px}

/* hero */
.hero{position:absolute;left:0;top:119px;width:1200px;height:455px;overflow:hidden}
.hero-photo{position:absolute;inset:0;background:
  radial-gradient(ellipse 420px 160px at 560px 330px,rgba(210,210,205,.55),transparent 70%),
  radial-gradient(ellipse 500px 300px at 1050px 300px,rgba(120,85,55,.55),transparent 70%),
  linear-gradient(180deg,#4a4744 0%,#5e5b57 45%,#2e2c2a 100%)}
.hero-shade{position:absolute;inset:0;background:rgba(0,0,0,.28)}
.hero-title{position:absolute;top:124px;width:1200px;font-family:var(--heading);font-weight:300;font-size:58px;color:var(--white);letter-spacing:1px}
.hero-sub{position:absolute;top:212px;width:1200px;font-family:var(--heading);font-size:21px;color:var(--white)}
.hero-btn-outline{position:absolute;left:428px;top:274px;width:167px;height:45px;border:1.5px solid var(--white);color:var(--white)}
.hero-btn-red{position:absolute;left:605px;top:274px;width:166px;height:45px}
.dots{position:absolute;display:flex;gap:6px}
.dots span{width:10px;height:10px;border-radius:50%;border:1.5px solid var(--white)}
.dots span.on{background:var(--white)}
.hero .dots{left:579px;top:401px}

/* section headings */
.section-title{position:absolute;width:1200px;font-family:var(--heading);font-weight:400;font-size:36px;color:var(--red);letter-spacing:.5px}
.lead{position:absolute;font-size:11.5px;line-height:21px;color:var(--muted)}

/* welcome */
.welcome{position:absolute;left:0;top:574px;width:1200px;height:449px;background:var(--white)}
.pillar{position:absolute;top:167px;width:360px;text-align:center}
.pillar-icon{width:98px;height:98px;border-radius:50%;border:1.5px solid var(--red);margin:0 auto;display:flex;align-items:center;justify-content:center}
.pillar-icon.filled{background:var(--red)}
.pillar h3{margin-top:22px;font-family:var(--heading);font-weight:400;font-size:25px;color:var(--red);letter-spacing:.5px}
.pillar p{margin-top:12px;font-size:11.5px;line-height:20px;color:var(--muted)}
.pillar a{display:block;margin-top:12px;font-size:11.5px;color:var(--red);text-decoration:none}

/* features */
.features{position:absolute;left:0;top:1023px;width:1200px;height:437px;background:var(--soft)}
.features .section-title{left:131px;width:auto;top:68px}
.feature{position:absolute;width:320px}
.feature-icon{position:absolute;left:0;top:0;width:45px;height:45px;border-radius:50%;border:1.5px solid var(--red);display:flex;align-items:center;justify-content:center}
.feature h4{position:absolute;left:62px;top:-12px;font-family:var(--heading);font-weight:400;font-size:20px;color:var(--red);white-space:nowrap}
.feature p{position:absolute;left:62px;top:16px;width:260px;font-size:11px;line-height:21px;color:var(--muted);white-space:nowrap}
.phone{position:absolute;left:843px;top:47px;width:175px;height:361px;border-radius:28px;background:linear-gradient(#f7f7f7,#e2e2e2);border:2px solid #cfcfcf}
.phone-screen{position:absolute;left:10px;top:46px;width:151px;height:262px;background:linear-gradient(180deg,#ffffff 0%,#ffffff 38%,#55636d 52%,#3b4750 100%)}
.phone-speaker{position:absolute;left:68px;top:24px;width:36px;height:4px;border-radius:2px;background:#bdbdbd}
.phone-home{position:absolute;left:70px;top:318px;width:32px;height:32px;border-radius:50%;border:2px solid #bdbdbd}

/* testimonials */
.testimonials{position:absolute;left:0;top:1460px;width:1200px;height:361px;overflow:hidden}
.band-fill{position:absolute;inset:0;background:
  linear-gradient(135deg,rgba(255,255,255,.05) 0 30%,transparent 30% 55%,rgba(0,0,0,.05) 55% 75%,transparent 75%),
  linear-gradient(160deg,#d9302f,#c5252a)}
.testimonials .section-title{top:70px;color:var(--white)}
.avatar{position:absolute;left:192px;top:167px;width:98px;height:98px;border-radius:50%;border:3px solid var(--white);background:radial-gradient(circle at 50% 40%,#c79a7e,#6a4a3c)}
.quote-card{position:absolute;left:332px;top:151px;width:567px;height:135px;background:var(--white);border-radius:3px}
.quote-card:before{content:"";position:absolute;left:-20px;top:46px;border:12px solid transparent;border-right:10px solid var(--white)}
.quote-text{position:absolute;left:56px;top:28px;width:470px;font-size:15px;line-height:21px;color:var(--red)}
.quote-name{position:absolute;left:56px;top:82px;font-size:14px;font-weight:600;color:var(--ink)}
.quote-stars{position:absolute;left:56px;top:104px}
.testimonials .dots{left:579px;top:321px}

/* contact */
.contact{position:absolute;left:0;top:1821px;width:1200px;height:531px;background:var(--white)}
.contact .section-title{top:48px}
.field{position:absolute;left:131px;width:423px;border:1.5px solid var(--line);border-radius:24px;font-family:var(--heading);font-size:12px;color:var(--muted);padding:0 22px;display:flex;align-items:center;text-transform:uppercase}
.field.area{align-items:flex-start;padding-top:30px;border-radius:30px}
.contact-submit{position:absolute;left:131px;top:446px;width:107px;height:35px;font-size:12px}
.contact-row{position:absolute;left:599px;width:520px}
.contact-icon{position:absolute;left:0;top:0;width:45px;height:45px;border-radius:50%;border:1.5px solid var(--red);display:flex;align-items:center;justify-content:center}
.contact-row p{position:absolute;left:64px;top:4px;width:330px;font-size:11.5px;line-height:21px;color:var(--muted)}

/* footer */
.site-footer{position:absolute;left:0;top:2352px;width:1200px;height:272px;overflow:hidden}
.footer-brand{position:absolute;top:88px;width:1200px;display:flex;justify-content:center}
.footer-brand .brand-name{color:var(--white);font-size:32px;line-height:40px}
.social{position:absolute;top:153px;left:0;width:1200px;height:45px}
.social span{position:absolute;top:0;width:45px;height:45px;border-radius:50%;border:1.5px solid var(--white)}
.copyright{position:absolute;top:218px;width:1200px;font-size:11.5px;color:var(--white)}
</style>
</head>
<body>

<header class="site-header">
  <div class="brand"><span class="brand-dot"></span><span class="brand-name">wooSpark.net</span></div>
  <nav class="main-nav">
    <a class="active" style="left:548px">Home</a>
    <a style="left:620px">About us</a>
    <a style="left:705px">Features</a>
    <a style="left:792px">Demo</a>
    <a style="left:861px">Contact us</a>
  </nav>
  <a class="btn btn-red nav-cta">Get App</a>
</header>

<section class="hero">
  <div class="hero-photo" role="img" aria-label="Blurred café photo with two coffee cups on a round table"></div>
  <div class="hero-shade"></div>
  <h1 class="hero-title center">MEET - PLAY - DATE</h1>
  <p class="hero-sub center">The game is Patent Pending</p>
  <a class="btn hero-btn-outline">Learn More</a>
  <a class="btn btn-red hero-btn-red">Get App</a>
  <div class="dots"><span class="on"></span><span></span><span></span></div>
</section>

<section class="welcome">
  <h2 class="section-title center" style="top:40px">WELCOME TO WOOSPARK</h2>
  <p class="lead center" style="left:240px;width:720px;top:90px">The app will be interactive and is designed to be a fun, safe and nonthreatening way to help two people get to know more about<br>each other before making a face to face date.</p>

  <div class="pillar" style="left:79px">
    <div class="pillar-icon filled">
      <svg width="44" height="40" viewBox="0 0 44 40" fill="none" stroke="#fff" stroke-width="2"><circle cx="16" cy="12" r="7"/><path d="M3 34c0-8 6-12 13-12s13 4 13 12z"/><path d="M26 6a7 7 0 1 1 2 13"/><path d="M31 22c6 1 10 5 10 12h-9"/></svg>
    </div>
    <h3>MEET</h3>
    <p>Browse profiles to find someone whom you want to<br>get to know better and invite them to play!</p>
    <a>MORE INFO</a>
  </div>
  <div class="pillar" style="left:420px">
    <div class="pillar-icon">
      <svg width="46" height="40" viewBox="0 0 46 40" fill="none" stroke="#e5322d" stroke-width="2"><path d="M23 37S3 24 3 12.5A10 10 0 0 1 23 8a10 10 0 0 1 20 4.5C43 24 23 37 23 37z"/></svg>
    </div>
    <h3>PLAY</h3>
    <p>Many dating sites take you through a set of ques-<br>tions before you upload a profile.</p>
    <a>MORE INFO</a>
  </div>
  <div class="pillar" style="left:759px">
    <div class="pillar-icon">
      <svg width="48" height="44" viewBox="0 0 48 44" fill="none" stroke="#e5322d" stroke-width="2"><path d="M6 16h28v12a12 12 0 0 1-12 12h-4A12 12 0 0 1 6 28z"/><path d="M34 19h4a5 5 0 0 1 0 10h-5"/><path d="M2 42h40"/><path d="M15 4v7M20 2v9M25 4v7"/></svg>
    </div>
    <h3>DATE</h3>
    <p>"Wouldn't it be great to get to know someone better<br>before making a date?"</p>
    <a>MORE INFO</a>
  </div>
</section>

<section class="features">
  <h2 class="section-title">OUR FEATURES</h2>
  <p class="lead" style="left:131px;top:128px;width:640px">The app will be interactive and is designed to be a fun, safe and nonthreatening way to help two people get to know more about<br>each other before making a face to face date.</p>

  <div class="feature" style="left:131px;top:216px">
    <div class="feature-icon"><svg width="22" height="22" viewBox="0 0 22 22" fill="none" stroke="#e5322d" stroke-width="1.5"><rect x="2" y="7" width="18" height="5"/><rect x="4" y="12" width="14" height="8"/><path d="M11 7v13M11 7C9 2 5 3 6 6M11 7c2-5 6-4 5-1"/></svg></div>
    <h4>FUN</h4>
    <p>Many dating sites take you through a set of ques-<br>tions before you upload a profile.</p>
  </div>
  <div class="feature" style="left:476px;top:216px">
    <div class="feature-icon"><svg width="22" height="22" viewBox="0 0 22 22" fill="none" stroke="#e5322d" stroke-width="1.5"><rect x="4" y="10" width="14" height="10" rx="1"/><path d="M7 10V7a4 4 0 0 1 8 0v3"/></svg></div>
    <h4>SAFE</h4>
    <p>Many dating sites take you through a set of ques-<br>tions before you upload a profile.</p>
  </div>
  <div class="feature" style="left:131px;top:314px">
    <div class="feature-icon"><svg width="22" height="22" viewBox="0 0 22 22" fill="none" stroke="#e5322d" stroke-width="1.5"><circle cx="11" cy="11" r="9"/><circle cx="8" cy="9" r=".8" fill="#e5322d"/><circle cx="14" cy="9" r=".8" fill="#e5322d"/><path d="M7 13a5 5 0 0 0 8 0"/></svg></div>
    <h4>NONTHREATENING</h4>
    <p>Many dating sites take you through a set of ques-<br>tions before you upload a profile.</p>
  </div>
  <div class="feature" style="left:476px;top:314px">
    <div class="feature-icon"><svg width="22" height="22" viewBox="0 0 22 22" fill="none" stroke="#e5322d" stroke-width="1.5"><path d="M11 2a7 7 0 0 0-4 12.7V17h8v-2.3A7 7 0 0 0 11 2z"/><path d="M8 20h6"/></svg></div>
    <h4>HELP TWO PEOPLE</h4>
    <p>Many dating sites take you through a set of ques-<br>tions before you upload a profile.</p>
  </div>

  <div class="phone">
    <span class="phone-speaker"></span>
    <div class="phone-screen" role="img" aria-label="App login screen shown on a phone"></div>
    <span class="phone-home"></span>
  </div>
</section>

<section class="testimonials">
  <div class="band-fill" role="img" aria-label="Red low-poly geometric background"></div>
  <h2 class="section-title center">TESTIMONIALS</h2>
  <div class="avatar" role="img" aria-label="Portrait photo of the reviewer"></div>
  <div class="quote-card">
    <p class="quote-text">The app will be interactive and is designed to be a fun, safe and nonthreatening way to help two people</p>
    <p class="quote-name">John Doe</p>
    <svg class="quote-stars" width="70" height="13" viewBox="0 0 70 13" fill="#c8262a">
      <defs>
        <path id="star" d="M6.5 0l1.9 4.2 4.6.4-3.5 3 1 4.5-4-2.4-4 2.4 1-4.5L0 4.6l4.6-.4z"/>
        <clipPath id="half"><rect x="56" y="0" width="6.5" height="13"/></clipPath>
      </defs>
      <use href="#star"/><use href="#star" x="14"/><use href="#star" x="28"/><use href="#star" x="42"/>
      <use href="#star" x="56" clip-path="url(#half)"/>
    </svg>
  </div>
  <div class="dots"><span class="on"></span><span></span><span></span></div>
</section>

<section class="contact">
  <h2 class="section-title center">CONTACT US</h2>
  <div class="field" style="top:136px;height:46px">Name</div>
  <div class="field" style="top:194px;height:46px">Email</div>
  <div class="field area" style="top:253px;height:177px">Message</div>
  <a class="btn btn-red contact-submit">Submit</a>

  <div class="contact-row" style="top:133px">
    <div class="contact-icon"><svg width="18" height="22" viewBox="0 0 18 22" fill="none" stroke="#e5322d" stroke-width="1.6"><path d="M9 21s7-7.5 7-12.5a7 7 0 0 0-14 0C2 13.5 9 21 9 21z"/><circle cx="9" cy="8.5" r="2.5" fill="#e5322d"/></svg></div>
    <p>Lorem ipsum dolor sit amet, consectetur adipiscing elit, sed do eiusmod tempor incididunt</p>
  </div>
  <div class="contact-row" style="top:195px">
    <div class="contact-icon"><svg width="22" height="16" viewBox="0 0 22 16" fill="none" stroke="#e5322d" stroke-width="1.6"><rect x="1" y="1" width="20" height="14" rx="1.5"/><path d="M1 2l10 8 10-8"/></svg></div>
    <p style="top:12px">hello@woospark.net</p>
  </div>
  <div class="contact-row" style="top:249px">
    <div class="contact-icon"><svg width="20" height="20" viewBox="0 0 20 20" fill="#e5322d"><path d="M4.6 1.5l2.6 3.6-1.7 2.2c.9 2.3 2.9 4.3 5.2 5.2l2.2-1.7 3.6 2.6-1.4 3.1c-.4.7-1.1 1-1.9.9C7 16.6 3.4 13 2.6 6.8c-.1-.8.2-1.5.9-1.9z"/></svg></div>
    <p style="top:12px">(555) 014 2290</p>
  </div>
</section>

<footer class="site-footer">
  <div class="band-fill" role="img" aria-label="Red low-poly geometric background"></div>
  <div class="footer-brand"><span class="brand-name">wooSpark.net</span></div>
  <div class="social" aria-label="Social links">
    <span style="left:523px"></span>
    <span style="left:577px"></span>
    <span style="left:631px"></span>
  </div>
  <p class="copyright center">Copyright © 2016 &nbsp;woospark.net. All Right Reserved</p>
</footer>

</body>
</html>
```